Business Card Design

We service, sell & install vehicle hoists in automotive workshops & would like the colours royal blue or green incorporated into the design.

Industry/Entity Type

Automotive

Contact Information for Business Card

KLT Lifts
Equipment Sales & Service
Colin Dwyer 0412 558 913
Grant Oakes 0418 762 305
14 Tarn Crescent Wyndale Vic 3521
email: kltlifts@mailbox-example.com.au

```html
<!DOCTYPE html>
<html lang="en">
<head>
<meta charset="utf-8">
<title>KLT Lifts – Business Card</title>
<link rel="stylesheet" href="https://fonts.googleapis.com/css2?family=Oswald:wght@400&family=Open+Sans:wght@300;400;700&display=swap">
<style>
  :root {
    --backdrop: #2b2b2b;
    --card: #f7f7f5;
    --ink: #1f1f1f;
    --ink-soft: #3a3a3a;
    --royal-blue: #2a52be;
    --royal-blue-deep: #1c3a8c;
  }
  * { margin: 0; padding: 0; box-sizing: border-box; }
  html, body {
    width: 1200px; height: 938px; overflow: hidden;
    background: var(--backdrop);
  }
  .card {
    position: absolute; left: 100px; top: 157px;
    width: 1000px; height: 624px;
    background: var(--card);
    font-family: "Open Sans", Arial, sans-serif;
    color: var(--ink);
    overflow: hidden;
  }
  .hoist-art {
    position: absolute; left: 50px; top: 0;
    width: 60px; height: 560px;
    background: linear-gradient(180deg, rgba(42, 82, 190, 0.12), rgba(42, 82, 190, 0.35));
  }
  .brand {
    position: absolute; left: 140px; top: 62px;
  }
  .brand-name {
    font-family: "Oswald", "Arial Narrow", sans-serif;
    font-weight: 400;
    font-size: 56px; line-height: 1;
    letter-spacing: 0.5px;
    color: var(--ink);
    text-transform: uppercase;
    white-space: nowrap;
  }
  .brand-tagline {
    margin-top: 8px;
    font-weight: 400;
    font-size: 32px; line-height: 1.1;
    color: var(--ink-soft);
  }
  .person-name {
    position: absolute; right: 68px; top: 336px;
    font-size: 50px; font-weight: 300;
    letter-spacing: 1px;
    text-transform: uppercase;
    white-space: nowrap;
  }
  .person-name .surname { font-weight: 700; }
  .contact-list {
    position: absolute; right: 62px; top: 440px;
    list-style: none; text-align: right;
  }
  .contact-item {
    display: flex; justify-content: flex-end; align-items: center;
    gap: 16px;
    height: 42px;
    font-size: 28px; font-weight: 400;
    color: var(--ink-soft);
    white-space: nowrap;
  }
  .contact-icon { width: 20px; height: 24px; flex: none; }
  .contact-icon * { fill: none; stroke: var(--royal-blue); stroke-width: 2.4; }
  .contact-icon .solid { fill: var(--royal-blue); stroke: none; }
  .hazard-band {
    position: absolute; left: 0; bottom: 0;
    width: 100%; height: 22px;
    background: linear-gradient(90deg, var(--royal-blue), var(--royal-blue-deep) 50%, var(--royal-blue));
  }
</style>
</head>
<body>
  <article class="card">
    <div class="hoist-art" role="img" aria-label="Hoist cable with a hanging lifting hook"></div>

    <header class="brand">
      <div class="brand-name">KLT Lifts Equipment</div>
      <div class="brand-tagline">Sales &amp; Service</div>
    </header>

    <h1 class="person-name">Colin <span class="surname">Dwyer</span></h1>

    <ul class="contact-list">
      <li class="contact-item">0412 558 913
        <svg class="contact-icon" viewBox="0 0 20 24" aria-hidden="true"><rect x="4" y="2" width="12" height="20" rx="2"/><rect class="solid" x="8" y="18" width="4" height="2"/></svg>
      </li>
      <li class="contact-item">Tarn Crescent Wyndale Vic 3521
        <svg class="contact-icon" viewBox="0 0 20 24" aria-hidden="true"><path class="solid" d="M10 2a7 7 0 0 0-7 7c0 5 7 13 7 13s7-8 7-13a7 7 0 0 0-7-7zm0 10a3 3 0 1 1 0-6 3 3 0 0 1 0 6z"/></svg>
      </li>
      <li class="contact-item">kltlifts@mailbox-example.com.au
        <svg class="contact-icon" viewBox="0 0 20 24" aria-hidden="true"><rect x="2" y="7" width="16" height="11"/><path d="M2 7l8 6 8-6"/></svg>
      </li>
    </ul>

    <div class="hazard-band" role="img" aria-label="Striped safety band along the bottom edge"></div>
  </article>
</body>
</html>
```